Veltrano.co - Polar Expeditions Specialists

We need a modern, visually striking business card for Veltrano.co, a company specialized in selling expedition cruises to the most remote regions on Earth, with a focus on the Arctic and Antarctica. The design should instantly communicate that the cardholder is an expert in polar travel. Use clean, premium aesthetics with cool tones like icy blue and white, possibly incorporating polar imagery (ice, glaciers, penguins, etc.)

Attached the logo

Contact Information for Business Card

Feels high-end and trustworthy.. Visually memorable — encourages people to keep it

Colors
0054AA
0677BA
7BADD7
CADEEF
E8F1F8

Requirements
Must have
• ice, glaciers, penguins, montains
Nice to have
• modern, transparente,

```html
<!DOCTYPE html>
<html lang="en">
<head>
<meta charset="utf-8">
<title>Veltrano.co – Business Card</title>
<link rel="stylesheet" href="https://fonts.googleapis.com/css2?family=Poppins:wght@400;600;700&display=swap">
<style>
  :root {
    --page-bg: #3a332e;
    --card-bg: #111112;
    --brand-blue: #3a78c2;
    --edge-blue: #2a67b0;
    --text-light: #e9eef4;
    --art-light: #5a5a5e;
    --art-dark: #1a1a1c;
  }
  * { box-sizing: border-box; margin: 0; padding: 0; }
  html, body { width: 1200px; height: 847px; overflow: hidden; }
  body {
    background: var(--page-bg);
    font-family: "Poppins", sans-serif;
    position: relative;
  }
  .card {
    position: absolute;
    width: 520px;
    height: 297px;
    background: var(--card-bg);
    border-bottom: 4px solid var(--edge-blue);
    overflow: hidden;
    box-shadow: 0 14px 30px rgba(0,0,0,.45);
  }
  .card--front { left: 50px; top: 275px; }
  .card--back { left: 630px; top: 275px; }

  .front-art {
    position: absolute;
    left: 0; top: 0;
    width: 250px; height: 293px;
    background: linear-gradient(160deg, var(--art-dark) 0%, #2c2c2f 45%, var(--art-light) 100%);
  }
  .front-brand {
    position: absolute;
    left: 266px; top: 196px;
  }
  .brand-name {
    color: var(--brand-blue);
    font-weight: 700;
    line-height: 1;
    white-space: nowrap;
  }
  .front-brand .brand-name { font-size: 38px; }
  .tagline {
    color: var(--brand-blue);
    font-weight: 600;
    font-size: 11px;
    margin-top: 6px;
    white-space: nowrap;
  }

  .back-brand {
    position: absolute;
    left: 150px; top: 58px;
    display: flex; align-items: center; gap: 14px;
  }
  .brand-mark {
    width: 16px; height: 16px; border-radius: 50%;
    background: var(--brand-blue);
    flex: none;
  }
  .back-brand .brand-name { font-size: 40px; }
  .back-brand .tagline { font-size: 12px; }

  .person {
    position: absolute;
    left: 30px; top: 185px;
    text-align: right;
    width: 185px;
  }
  .person-name {
    color: var(--brand-blue);
    font-weight: 700;
    font-size: 17px;
    text-transform: uppercase;
    white-space: nowrap;
  }
  .person-title {
    color: var(--text-light);
    font-size: 13px;
  }
  .divider {
    position: absolute;
    left: 238px; top: 180px;
    width: 1px; height: 62px;
    background: var(--brand-blue);
  }
  .contact {
    position: absolute;
    left: 258px; top: 178px;
    list-style: none;
  }
  .contact li {
    display: flex; align-items: center; gap: 8px;
    color: var(--text-light);
    font-size: 13px;
    line-height: 22px;
    white-space: nowrap;
  }
  .contact svg { width: 12px; height: 12px; fill: var(--brand-blue); flex: none; }
</style>
</head>
<body>
  <section class="card card--front">
    <div class="front-art" role="img" aria-label="Glossy dark silhouette of a polar bear with penguins"></div>
    <div class="front-brand">
      <p class="brand-name">Veltrano.co</p>
      <p class="tagline">Polar Expeditions Specialists</p>
    </div>
  </section>

  <section class="card card--back">
    <div class="back-brand">
      <span class="brand-mark"></span>
      <div>
        <p class="brand-name">Veltrano.co</p>
        <p class="tagline">Polar Expeditions Specialists</p>
      </div>
    </div>

    <div class="person">
      <p class="person-name">Marek Lindqvist</p>
      <p class="person-title">President</p>
    </div>
    <div class="divider"></div>
    <ul class="contact">
      <li>
        <svg viewBox="0 0 24 24"><path d="M6.6 10.8a15 15 0 0 0 6.6 6.6l2.2-2.2a1 1 0 0 1 1-.25 11.4 11.4 0 0 0 3.6.57 1 1 0 0 1 1 1V20a1 1 0 0 1-1 1A17 17 0 0 1 3 4a1 1 0 0 1 1-1h3.5a1 1 0 0 1 1 1c0 1.25.2 2.45.57 3.57a1 1 0 0 1-.25 1z"/></svg>
        555-318-7024
      </li>
      <li>
        <svg viewBox="0 0 24 24"><path d="M2 5h20v14H2zM3 6l9 7 9-7v2l-9 7-9-7z"/></svg>
        mlindqvist@veltrano.co
      </li>
      <li>
        <svg viewBox="0 0 24 24"><path d="M12 2a10 10 0 1 0 0 20 10 10 0 0 0 0-20zm6.9 6h-3a15.6 15.6 0 0 0-1.4-3.6A8 8 0 0 1 18.9 8zM12 4c.8 1.2 1.5 2.5 1.9 4h-3.8c.4-1.5 1.1-2.8 1.9-4zM4.3 14a8 8 0 0 1 0-4h3.4a16 16 0 0 0 0 4zm.8 2h3a15.6 15.6 0 0 0 1.4 3.6A8 8 0 0 1 5.1 16zm3-8h-3a8 8 0 0 1 4.4-3.6A15.6 15.6 0 0 0 8.1 8zM12 20c-.8-1.2-1.5-2.5-1.9-4h3.8c-.4 1.5-1.1 2.8-1.9 4zm2.3-6H9.7a14.7 14.7 0 0 1 0-4h4.6a14.7 14.7 0 0 1 0 4zm.2 5.6a15.6 15.6 0 0 0 1.4-3.6h3a8 8 0 0 1-4.4 3.6zm1.8-5.6a16 16 0 0 0 0-4h3.4a8 8 0 0 1 0 4z"/></svg>
        www.veltrano.co
      </li>
    </ul>
  </section>
</body>
</html>
```